Tall Fern Roofing Business Card

Need a business card with the logo that was designed here

Contact Information for Business Card

Name, Title, Phone, Email, Website, Company name

```html
<!DOCTYPE html>
<html lang="en">
<head>
<meta charset="utf-8">
<title>Tall Fern Roofing Business Card</title>
<link rel="stylesheet" href="https://fonts.googleapis.com/css2?family=Montserrat:wght@400;500;700&display=swap">
<style>
  :root {
    --canvas-bg: #c9c9c9;
    --card-grey: #7e7e80;
    --accent-blue: #3b6fc6;
    --stripe-white: #f4f4f6;
    --text-white: #ffffff;
    --silver: #d8d8da;
  }
  * { margin: 0; padding: 0; box-sizing: border-box; }
  html, body { width: 1200px; height: 788px; overflow: hidden; }
  body {
    background: linear-gradient(160deg, #d6d6d6 0%, var(--canvas-bg) 60%, #b9b9b9 100%);
    font-family: "Montserrat", sans-serif;
    position: relative;
  }
  .card {
    position: absolute;
    width: 540px;
    height: 310px;
    border-radius: 22px;
    background: var(--card-grey);
    overflow: hidden;
    box-shadow: 0 14px 30px rgba(0,0,0,0.28);
  }
  .card--front { left: 40px; top: 120px; }
  .card--back { left: 620px; top: 358px; }

  /* front */
  .bottom-stripe {
    position: absolute; left: 0; right: 0; bottom: 0; height: 12px;
    display: flex;
  }
  .bottom-stripe__blue { flex: 0 0 58%; background: var(--accent-blue); }
  .bottom-stripe__white { flex: 1; background: var(--stripe-white); }

  .name-tab {
    position: absolute; left: 0; top: 150px;
    width: 10px; height: 48px; background: var(--accent-blue);
  }
  .person { position: absolute; left: 32px; top: 148px; }
  .person__name {
    color: var(--accent-blue); font-weight: 700; font-size: 21px; letter-spacing: 1.5px;
    white-space: nowrap;
  }
  .person__title {
    color: var(--text-white); font-weight: 500; font-size: 13px; margin-top: 4px; letter-spacing: 0.4px;
  }

  .roof-graphic {
    position: absolute; left: 180px; top: 218px; width: 130px; height: 80px;
    background: linear-gradient(135deg, #a4a4a6 0%, #5a5a5c 100%);
    border-radius: 4px 4px 0 0; opacity: 0.85;
  }

  .brand-front {
    position: absolute; right: 34px; top: 40px;
    color: var(--text-white); font-weight: 700; font-size: 24px; letter-spacing: 0.3px;
    white-space: nowrap;
  }

  .contact {
    position: absolute; left: 330px; top: 96px;
    color: var(--text-white); font-size: 12.5px; font-weight: 500; line-height: 1.55;
    white-space: nowrap;
  }
  .contact__address { margin-bottom: 10px; }
  .contact__row { display: flex; align-items: center; gap: 8px; }
  .contact__icon { width: 11px; height: 11px; flex: none; }

  /* back */
  .brand-back {
    position: absolute; left: 0; right: 0; top: 128px; text-align: center;
    color: var(--silver); font-weight: 700; font-size: 38px; letter-spacing: 0.5px;
  }
</style>
</head>
<body>

<section class="card card--front" aria-label="Business card front">
  <div class="brand-front">Tall Fern Roofing</div>

  <div class="contact">
    <div class="contact__address">418 Ridgeway Avenue<br>Harlow County Name 5120</div>
    <div class="contact__row">
      <svg class="contact__icon" viewBox="0 0 12 12" aria-hidden="true"><circle cx="6" cy="6" r="6" fill="#3b6fc6"/><path d="M3.5 3.2l1.3-.4.8 1.7-.8.6a4 4 0 0 0 1.9 1.9l.6-.8 1.7.8-.4 1.3C6.3 8.4 3.6 5.7 3.5 3.2z" fill="#fff"/></svg>
      <span>0412 555 019</span>
    </div>
    <div class="contact__row">
      <svg class="contact__icon" viewBox="0 0 12 12" aria-hidden="true"><circle cx="6" cy="6" r="6" fill="#3b6fc6"/><rect x="3" y="4" width="6" height="4.2" fill="#fff"/><path d="M3 4l3 2.3L9 4" stroke="#3b6fc6" stroke-width="0.7" fill="none"/></svg>
      <span>info@tallfernroofing.com</span>
    </div>
    <div class="contact__row">
      <svg class="contact__icon" viewBox="0 0 12 12" aria-hidden="true"><circle cx="6" cy="6" r="6" fill="#3b6fc6"/><circle cx="6" cy="6" r="3" fill="none" stroke="#fff" stroke-width="0.8"/><path d="M3 6h6M6 3v6" stroke="#fff" stroke-width="0.7"/></svg>
      <span>www.tallfernroofing.com</span>
    </div>
  </div>

  <div class="name-tab"></div>
  <div class="person">
    <div class="person__name">MARCUS DELANEY</div>
    <div class="person__title">Managing Director</div>
  </div>

  <div class="roof-graphic" role="img" aria-label="Large decorative roof graphic area"></div>

  <div class="bottom-stripe">
    <div class="bottom-stripe__blue"></div>
    <div class="bottom-stripe__white"></div>
  </div>
</section>

<section class="card card--back" aria-label="Business card back">
  <div class="brand-back">Tall Fern Roofing</div>
</section>

</body>
</html>
```